KRL Stationery Design Project

Dear Designers,
We need a new stationery design for company to match our new logo.
Designers should provide a design for the following:
1. Business Card: 3.5x2 Inches.
2. Letterhead: A4 size.
3. Envelops: 25x35.5 Cm.
You can keep the Arabic name at the bottom of the logo Or you can use the separate attached Arabic Name.
Please refer to the attached logo guide for design information.
Sample Business Card information:
Name: Tarek Sowan
Position: Operation Manager
Tel: +966 920007164 Ex. 500
Fax: +966 (3)8842617
Mob: +966 (5)00263817
email: tarek@krl-example.com.sa
URL: www.krl-example.com.sa
Address:
Nakheel Heights, Suite 718
Zayed bin Omar Str.
Khobar, 31847
Saudi Arabia
Updates
Dear All,
Please note, we had uploaded our logo along with Arabic writing in Adobe illustrator format (.ai).
Regards,
Karim
Dear All,
A sample data for the business card had been added as per your request.
Regards,
Karim

```html
<!DOCTYPE html>
<html lang="en">
<head>
<meta charset="utf-8">
<title>KRL Business Card</title>
<link href="https://fonts.googleapis.com/css2?family=Signika:wght@400;600;700&display=swap" rel="stylesheet">
<style>
  :root {
    --navy: #112b55;
    --grey: #9a9ca1;
    --ink: #2c2c2c;
    --paper: #ffffff;
    --stage: #e9e9ea;
  }
  * { margin: 0; padding: 0; box-sizing: border-box; }
  html, body { width: 1200px; height: 472px; overflow: hidden; }
  body {
    background: var(--stage);
    font-family: "Signika", Arial, sans-serif;
    position: relative;
  }
  .card {
    position: absolute;
    top: 85px;
    width: 522px;
    height: 300px;
    border-radius: 20px;
    overflow: hidden;
  }
  .card-front { left: 62px; background: var(--paper); }
  .card-back { left: 604px; background: var(--navy); }

  .front-brand {
    position: absolute;
    top: 30px; left: 0; width: 100%;
    display: flex; justify-content: center; align-items: center; gap: 14px;
  }
  .brand-mark { width: 22px; height: 22px; background: var(--navy); }
  .brand-name {
    font-weight: 700;
    font-size: 72px;
    line-height: 1;
    color: var(--navy);
    letter-spacing: 2px;
  }

  .address {
    position: absolute;
    right: 269px; top: 181px;
    text-align: right;
    font-size: 13.5px;
    line-height: 18px;
    color: var(--ink);
  }
  .divider {
    position: absolute;
    left: 268px; top: 163px;
    width: 1px; height: 78px;
    background: #b5b5b5;
  }
  .contacts {
    position: absolute;
    left: 282px; top: 164px;
    list-style: none;
    font-size: 13.5px;
    line-height: 17px;
    color: var(--ink);
  }
  .contacts li { display: flex; align-items: center; gap: 7px; }
  .contacts svg { width: 11px; height: 11px; fill: var(--navy); }

  .front-swoosh { position: absolute; left: 0; top: 0; width: 522px; height: 300px; }
  .holder {
    position: absolute;
    bottom: 10px; left: 0; width: 100%;
    text-align: center;
    color: var(--paper);
    font-size: 19px;
  }
  .holder-name { font-weight: 700; }
  .holder-title { font-weight: 400; font-size: 15px; }

  .back-frame {
    position: absolute;
    left: 12px; top: 45px;
    width: 490px; height: 200px;
    border: 7px solid var(--grey);
    border-radius: 26px;
  }
  .back-brand {
    position: absolute;
    top: 105px; left: 0; width: 100%;
    display: flex; justify-content: center; align-items: center; gap: 16px;
  }
  .back-brand .brand-mark { background: var(--paper); width: 24px; height: 24px; }
  .back-brand .brand-name { color: var(--paper); font-size: 84px; }
  .back-web {
    position: absolute;
    bottom: 20px; left: 0; width: 100%;
    text-align: center;
    color: var(--paper);
    font-size: 13px;
    letter-spacing: 3px;
  }
</style>
</head>
<body>
  <section class="card card-front">
    <svg class="front-swoosh" viewBox="0 0 522 300" aria-hidden="true">
      <path d="M0,195 Q170,248 522,258 Q190,256 0,219 Z" fill="var(--grey)"/>
      <path d="M0,222 Q190,262 522,262 L522,300 L0,300 Z" fill="var(--navy)"/>
    </svg>

    <div class="front-brand">
      <span class="brand-mark"></span>
      <span class="brand-name">KRL</span>
    </div>

    <p class="address">Street Name, City Name<br>State, City Zip Code</p>
    <div class="divider"></div>
    <ul class="contacts">
      <li><svg viewBox="0 0 12 12"><path d="M2 1h3l1 3-2 1a7 7 0 0 0 3 3l1-2 3 1v3c-6 0-9-3-9-9z"/></svg>123-456-7890</li>
      <li><svg viewBox="0 0 12 12"><path d="M2 5l1.5-3h5L10 5h1v4H9v1H7V9H5v1H3V9H1V5z"/></svg>123-456-7890</li>
      <li><svg viewBox="0 0 12 12"><path d="M1 3h10v7H1z M1 3l5 4 5-4"/></svg>info@krl-example.com.sa</li>
      <li><svg viewBox="0 0 12 12"><circle cx="6" cy="6" r="5"/></svg>www.website.com</li>
    </ul>

    <p class="holder"><span class="holder-name">Your Name,</span> <span class="holder-title">Title</span></p>
  </section>

  <section class="card card-back">
    <div class="back-frame"></div>
    <div class="back-brand">
      <span class="brand-mark"></span>
      <span class="brand-name">KRL</span>
    </div>
    <p class="back-web">www.website.com</p>
  </section>
</body>
</html>
```